Real estate broker business card

Want a modern celan but effective business card for my residential and commercial real estate business. I want the back of the card to advertise my services and to capture business. I have attached the back of my current business card fore ideas
Updates

Logos, photo and text updates added! Added Saturday, September 3, 2016

Project Deadline Extended Reason: LOGOS, PHOTOS AND TEST JUST UPLOADED! I'M READY TO PICK A DESIGN! THANK YOU! Added Saturday, September 3, 2016

Target Market(s)

home buyers and seller. commercial buyers and sellers

Industry/Entity Type

Real Estate

Contact Information for Business Card

must have my contact information and my photo

Requirements
Must have
• Carla Ventrino
• Owner & Qualifying Broker
• Ventrino Real Estate Services
• 505.718.2094
• carla@ventrinohomes.example
• www.ventrinohomes.example
Nice to have
• metallic
• Business capture text: " Don't buy or lease property without someone looking out for your best interests. I will represent you on your home or investment purchase for FREE!"
• "Home owners, call today to receive a FREE market analysis for your homes value!

```html
<!DOCTYPE html>
<html lang="en">
<head>
<meta charset="utf-8">
<title>Ventrino Real Estate Services – Business Card</title>
<link href="https://fonts.googleapis.com/css2?family=Cinzel:wght@700&family=Montserrat:wght@400;600&display=swap" rel="stylesheet">
<style>
  :root {
    --backdrop: #2a2a2c;
    --card: #0a0a0a;
    --teal: #2b7f8a;
    --white: #ffffff;
    --photo-top: #3f5a3c;
    --photo-bottom: #8a7a72;
  }
  * { box-sizing: border-box; margin: 0; padding: 0; }
  html, body { width: 1200px; height: 900px; overflow: hidden; }
  body {
    background: var(--backdrop);
    position: relative;
    font-family: "Montserrat", Arial, sans-serif;
  }
  .card {
    position: absolute;
    width: 640px;
    height: 366px;
    background: var(--card);
    border-radius: 22px;
    overflow: hidden;
    box-shadow: 0 18px 40px rgba(0,0,0,.45);
  }

  /* ---------- Back side ---------- */
  .card--back { left: 110px; top: 56px; }
  .back__brand {
    position: absolute; top: 70px; left: 0; right: 0;
    text-align: center;
    font-family: "Cinzel", Georgia, serif;
    font-weight: 700;
    font-size: 24px;
    letter-spacing: 1px;
    color: var(--teal);
  }
  .back__pitch {
    position: absolute; top: 150px; left: 80px; right: 80px;
    text-align: center;
    color: var(--white);
    font-size: 15px;
    line-height: 1.4;
  }
  .back__pitch p + p { margin-top: 14px; }
  .back__pitch strong { font-weight: 600; }

  /* ---------- Front side ---------- */
  .card--front { left: 450px; top: 478px; }
  .front__bands { position: absolute; inset: 0; }
  .front__brand {
    position: absolute; left: 34px; top: 112px;
    display: flex; align-items: center; gap: 14px;
  }
  .front__brand-dot {
    width: 14px; height: 14px; border-radius: 50%;
    background: var(--teal);
    flex: none;
  }
  .front__brand-name {
    font-family: "Cinzel", Georgia, serif;
    font-weight: 700;
    font-size: 22px;
    line-height: 1.15;
    letter-spacing: .5px;
    color: var(--teal);
  }
  .front__photo {
    position: absolute; right: 44px; top: 24px;
    width: 196px; height: 150px;
    border: 3px solid var(--white);
    background: linear-gradient(160deg, var(--photo-top), var(--photo-bottom));
  }
  .front__person {
    position: absolute; right: 44px; top: 184px;
    text-align: right;
  }
  .front__name {
    font-family: "Cinzel", Georgia, serif;
    font-weight: 700;
    font-size: 24px;
    color: var(--teal);
    padding-bottom: 3px;
    border-bottom: 2px solid var(--white);
  }
  .front__title {
    margin-top: 4px;
    font-size: 15px;
    color: var(--white);
  }
  .front__contacts {
    position: absolute; left: 34px; top: 268px;
    list-style: none;
    color: var(--white);
    font-size: 16px;
  }
  .front__contacts li {
    display: flex; align-items: center; gap: 12px;
    height: 23px;
  }
  .front__contacts svg { width: 12px; height: 12px; flex: none; }
</style>
</head>
<body>

  <section class="card card--back" aria-label="Business card, back">
    <div class="back__brand">Ventrino Real Estate Services</div>
    <div class="back__pitch">
      <p>Don't buy or lease property without someone looking out for your best interests. I will represent you on your home or investment purchase for <strong>FREE</strong>!</p>
      <p>Home owners, call today to receive a <strong>FREE</strong> market analysis for your homes value!</p>
    </div>
  </section>

  <section class="card card--front" aria-label="Business card, front">
    <svg class="front__bands" viewBox="0 0 640 366" width="640" height="366" aria-hidden="true">
      <line x1="22" y1="262" x2="470" y2="262" stroke="#ffffff" stroke-width="1.5"/>
      <polygon points="0,360 470,344 470,366 0,366" fill="#ffffff"/>
      <polygon points="488,256 640,256 640,366 470,366" fill="#2b7f8a"/>
      <line x1="470" y1="254" x2="640" y2="254" stroke="#ffffff" stroke-width="1.5"/>
    </svg>

    <div class="front__brand">
      <span class="front__brand-dot"></span>
      <span class="front__brand-name">Ventrino<br>Real Estate Services</span>
    </div>

    <div class="front__photo" role="img" aria-label="Portrait photo of Carla Ventrino"></div>

    <div class="front__person">
      <div class="front__name">CARLA VENTRINO</div>
      <div class="front__title">Owner &amp; Qualifying Broker</div>
    </div>

    <ul class="front__contacts">
      <li>
        <svg viewBox="0 0 12 12"><path d="M2.5 1 L4.5 1 L5.2 3.6 L4 4.6 Q5 7 7.4 8 L8.4 6.8 L11 7.5 L11 9.5 Q11 11 9.5 11 Q1 10 1 2.5 Q1 1 2.5 1Z" fill="#2b7f8a"/></svg>
        505.718.2094
      </li>
      <li>
        <svg viewBox="0 0 12 12"><rect x="1" y="2.5" width="10" height="7" fill="none" stroke="#2b7f8a" stroke-width="1.3"/><polyline points="1,2.5 6,6.5 11,2.5" fill="none" stroke="#2b7f8a" stroke-width="1.3"/></svg>
        carla@ventrinohomes.example
      </li>
      <li>
        <svg viewBox="0 0 12 12"><circle cx="6" cy="6" r="5" fill="none" stroke="#2b7f8a" stroke-width="1.2"/><ellipse cx="6" cy="6" rx="2.2" ry="5" fill="none" stroke="#2b7f8a" stroke-width="1"/><line x1="1" y1="6" x2="11" y2="6" stroke="#2b7f8a" stroke-width="1"/></svg>
        www.ventrinohomes.example
      </li>
    </ul>
  </section>

</body>
</html>
```